New Baby Formula Company Needs a Shopify Website Design

We are launching a baby formula company and need a Shopify website design. We have a patented product that is a disposable pouch with a frangible seal through the middle. The top half contains formula powder and the bottom half contains purified water. There is also a bottle nipple on the corner under the cap in order to feed the baby. You just need to squeeze the bottom half of the pouch to break the seal and then the water and formula will mix. You then only need to shake it and then remove the cap and feed the baby. We will also sell formula in containers like the other formula companies. We want this website to stand out and look professional. We don't want a boring layout, but something unique and captivating. I have attached a mockup rendering of our product, though it's not the finished product and our logo. This will let you know the color scheme we are going for. Let me know if you have any further questions. Thank you

```html
<!DOCTYPE html>
<html lang="en">
<head>
<meta charset="utf-8">
<title>MILAVO — Baby Formula</title>
<link href="https://fonts.googleapis.com/css2?family=Lato:wght@400;700&display=swap" rel="stylesheet">
<style>
:root{
  --green:#a2b02e;
  --green-dark:#8e9c22;
  --ink:#333333;
  --text:#555555;
  --muted:#777777;
  --line:#ececec;
  --white:#ffffff;
  --star:#e0c23a;
}
*{box-sizing:border-box;margin:0;padding:0}
html,body{width:1200px;height:4425px;overflow:hidden}
body{position:relative;background:var(--white);font-family:'Lato',sans-serif;color:var(--text)}
.abs{position:absolute}
a{color:inherit;text-decoration:none}

/* header */
.topbar{left:112px;top:12px;font-size:12px;color:var(--text)}
.topbar span{color:var(--green)}
.currency{right:112px;top:8px;font-size:12px;color:var(--text)}
.brand{left:112px;top:48px;width:106px;height:98px;display:flex;align-items:center;gap:6px}
.brand-dot{width:14px;height:14px;border-radius:50%;background:var(--green)}
.brand-name{font-size:20px;font-weight:700;color:var(--green);letter-spacing:1px}
.nav{left:371px;top:90px;display:flex;gap:27px;font-size:14px;color:var(--ink)}
.header-icons{left:915px;top:88px;display:flex;gap:26px}
.header-icons svg{width:22px;height:22px;stroke:var(--green);fill:none;stroke-width:1.6}

/* hero */
.hero{left:0;top:163px;width:1200px;height:558px;background:var(--green)}
.hero-title{left:112px;top:275px;font-size:61px;font-weight:700;line-height:69px;color:var(--white)}
.hero-text{left:112px;top:434px;width:430px;font-size:19px;line-height:26px;color:var(--white)}
.btn-white{background:var(--white);color:var(--green);font-size:16px;display:flex;align-items:center;justify-content:center}
.hero-btn{left:112px;top:555px;width:154px;height:42px}
.hero-photo{left:594px;top:239px;width:493px;height:407px;background:linear-gradient(135deg,#d9c7bd,#c08f78 45%,#2d7fb3 70%,#4f6a86)}

/* intro */
.intro{left:150px;top:800px;width:900px;text-align:center;font-size:42px;font-weight:700;line-height:52px;color:var(--ink)}
.intro-link{left:0;width:1200px;top:972px;text-align:center;font-size:19px;color:var(--green)}

/* features */
.feature{top:1078px;width:302px;height:304px;border:1px solid var(--line);border-top:8px solid var(--green);box-shadow:0 2px 8px rgba(0,0,0,.05);padding:38px 38px 0}
.feature svg{width:70px;height:70px;stroke:var(--green);fill:none;stroke-width:2}
.feature h3{margin-top:30px;font-size:25px;font-weight:700;color:var(--green)}
.feature p{margin-top:12px;font-size:14px;line-height:23px;color:var(--text)}

/* about */
.about-photo{left:112px;top:1470px;width:482px;height:400px;background:linear-gradient(120deg,#5a5248,#c9a88a 45%,#e6d9cb 70%,#8b8f8f)}
.about-title{left:682px;top:1498px;font-size:42px;font-weight:700;color:var(--ink)}
.about-text{left:678px;top:1582px;width:410px;font-size:14px;line-height:24px;color:var(--text)}
.btn-green{background:var(--green);color:var(--white);font-size:15px;display:flex;align-items:center;justify-content:center}
.about-btn{left:678px;top:1789px;width:155px;height:43px}

/* products */
.section-title{left:0;width:1200px;text-align:center;font-size:42px;font-weight:700;color:var(--ink)}
.product{top:2031px;width:237px;height:313px;border:1px solid var(--line);box-shadow:0 2px 8px rgba(0,0,0,.05);text-align:center}
.product-img{width:120px;height:175px;margin:38px auto 0;border-radius:8px}
.product h4{margin-top:20px;font-size:21px;font-weight:700;color:var(--green)}
.product p{margin-top:8px;font-size:17px;color:var(--text)}
.dots{left:0;width:1200px;top:2376px;display:flex;justify-content:center;gap:16px;align-items:center}
.dots i{width:6px;height:6px;border-radius:50%;background:#cfcfcf;display:block}
.dots i.on{width:12px;height:12px;border:2px solid var(--green);background:var(--white)}

/* shipping */
.ship-photo{left:112px;top:2478px;width:487px;height:400px;background:radial-gradient(circle at 40% 45%,#f2ece0,#b9a68c 40%,#6e6358 80%)}
.ship-panel{left:599px;top:2478px;width:488px;height:400px;background:var(--green)}
.ship-title{left:660px;top:2520px;font-size:42px;font-weight:700;line-height:51px;color:var(--white)}
.ship-text{left:660px;top:2653px;width:360px;font-size:14px;line-height:24px;color:var(--white)}
.ship-btn{left:659px;top:2782px;width:153px;height:41px}

/* testimonials */
.clients-sub{left:0;width:1200px;top:3030px;text-align:center;font-size:20px;line-height:28px;color:var(--ink)}
.review{top:3108px;width:311px;height:293px;border:1px solid var(--line);box-shadow:0 2px 8px rgba(0,0,0,.05);text-align:center;padding-top:28px}
.review .meta{font-size:15px;color:var(--ink)}
.review .meta span{color:var(--green)}
.review .stars{margin-top:12px;font-size:20px;color:var(--star);letter-spacing:4px}
.review p{margin:14px auto 0;width:250px;font-size:14px;line-height:20px;color:var(--text)}
.review .who{margin-top:18px;display:flex;justify-content:center;align-items:center;gap:16px;font-size:15px;color:var(--green)}
.avatar{width:42px;height:42px;border-radius:50%}
.arrow{font-size:26px;color:var(--green)}

/* news */
.news-title{left:112px;top:3478px;font-size:42px;font-weight:700;color:var(--ink)}
.news{top:3573px;width:316px;height:407px;border:1px solid var(--line);box-shadow:0 2px 8px rgba(0,0,0,.05)}
.news-img{height:235px}
.news .date{margin:30px 0 0 22px;font-size:13px;color:var(--ink)}
.news h4{margin:14px 20px 0 22px;font-size:20px;font-weight:400;line-height:27px;color:var(--ink)}
.news .more{margin:12px 0 0 22px;font-size:16px;color:var(--green)}

/* footer */
.footer-brand{left:112px;top:4069px;width:110px;height:107px}
.footer-about{left:112px;top:4203px;width:270px;font-size:14px;line-height:24px;color:var(--text)}
.footer-col{top:4069px}
.footer-col h5{font-size:20px;font-weight:700;color:var(--green);margin-bottom:18px}
.footer-col li{list-style:none;font-size:14px;line-height:27.5px;color:var(--text)}
.to-top{left:1066px;top:4289px;width:43px;height:41px;background:var(--green);color:var(--white);display:flex;align-items:center;justify-content:center;font-size:14px}
.copyright{left:112px;top:4380px;font-size:12px;color:var(--ink)}
.socials{left:998px;top:4382px;display:flex;gap:11px}
.socials i{display:block;width:14px;height:14px;background:var(--green);border-radius:2px}
</style>
</head>
<body>

<div class="abs topbar">Call Us : <span>+1 555 010 0199</span></div>
<div class="abs currency">USD ⌄</div>
<div class="abs brand"><span class="brand-dot"></span><span class="brand-name">MILAVO</span></div>
<nav class="abs nav"><a>Home</a><a>About Us</a><a>Shop</a><a>Products</a><a>Blog</a><a>Contact Us</a></nav>
<div class="abs header-icons">
  <svg viewBox="0 0 24 24"><circle cx="10.5" cy="10.5" r="6.5"/><path d="M15.5 15.5L21 21"/></svg>
  <svg viewBox="0 0 24 24"><circle cx="12" cy="8" r="4"/><path d="M4 21c1-4.5 4-6.5 8-6.5s7 2 8 6.5"/></svg>
  <svg viewBox="0 0 24 24"><path d="M12 20s-8-5-8-11a4.5 4.5 0 0 1 8-2.8A4.5 4.5 0 0 1 20 9c0 6-8 11-8 11z"/></svg>
  <svg viewBox="0 0 24 24"><rect x="4" y="7" width="16" height="14" rx="2"/><path d="M8.5 10V6a3.5 3.5 0 0 1 7 0v4"/></svg>
</div>

<section class="abs hero"></section>
<h1 class="abs hero-title">WELCOME TO<br>MILAVO</h1>
<p class="abs hero-text">Excepteur sint occaecat cupidatat non proident, sunt in culpa qui officia deserunt mollit anim id est laborum.</p>
<a class="abs btn-white hero-btn">Shop Now</a>
<div class="abs hero-photo" role="img" aria-label="Parent feeding a baby from a bottle"></div>

<h2 class="abs intro">Lorem ipsum dolor sit amet, consectetur adipiscing elit, sed do eiusmod tempor ut labore et dolore magna aliqua.</h2>
<a class="abs intro-link">Contact Us →</a>

<div class="abs feature" style="left:112px">
  <svg viewBox="0 0 70 70"><circle cx="35" cy="37" r="24"/><path d="M28 13c3-4 10-4 12 1"/></svg>
  <h3>Lorem Ipsum</h3>
  <p>Lorem ipsum dolor sit amet, consectetur adipiscing elit, sed labore et dolore magna aliqua.</p>
</div>
<div class="abs feature" style="left:448px">
  <svg viewBox="0 0 70 70"><circle cx="35" cy="24" r="15"/><path d="M28 24l5 5 9-10"/><path d="M8 42l10 18h10M62 42L52 60H42"/></svg>
  <h3>Sed ut perspiciatis</h3>
  <p>Lorem ipsum dolor sit amet, consectetur adipiscing elit, sed labore et dolore magna aliqua.</p>
</div>
<div class="abs feature" style="left:785px">
  <svg viewBox="0 0 70 70"><rect x="5" y="18" width="38" height="28" rx="2"/><path d="M43 27h12l9 10v9H43z"/><circle cx="17" cy="50" r="5"/><circle cx="52" cy="50" r="5"/></svg>
  <h3>Excepteur sint</h3>
  <p>Lorem ipsum dolor sit amet, consectetur adipiscing elit, sed labore et dolore magna aliqua.</p>
</div>

<div class="abs about-photo" role="img" aria-label="Mother smiling while bottle feeding her baby"></div>
<h2 class="abs about-title">About Us</h2>
<p class="abs about-text">Sed ut perspiciatis unde omnis iste natus error sit voluptatem accusantium doloremque laudantium, totam rem aperiam, eaque ipsa quae ab illo inventore veritatis et quasi architecto beatae vitae dicta sunt explicabo. Nemo enim ipsam voluptatem quia voluptas sit aspernatur aut odit aut fugit, sed quia consequuntur magni dolores eos qui ratione voluptatem sequi nesciunt.</p>
<a class="abs btn-green about-btn">Read More</a>

<h2 class="abs section-title" style="top:1948px">Our Products</h2>
<div class="abs product" style="left:112px"><div class="product-img" role="img" aria-label="Green formula pouch" style="background:linear-gradient(160deg,#f1f3e0,#a9b84a)"></div><h4>Lorem Ipsum</h4><p>$ 150.00</p></div>
<div class="abs product" style="left:357px"><div class="product-img" role="img" aria-label="White formula tin" style="background:linear-gradient(90deg,#e4e4e4,#ffffff 50%,#dcdcdc)"></div><h4>Lorem Ipsum</h4><p>$ 150.00</p></div>
<div class="abs product" style="left:604px"><div class="product-img" role="img" aria-label="Striped silver formula tin" style="background:linear-gradient(90deg,#9aa0a6,#f4f4f4 50%,#7f858b)"></div><h4>Lorem Ipsum</h4><p>$ 150.00</p></div>
<div class="abs product" style="left:850px"><div class="product-img" role="img" aria-label="Formula pouch back side" style="background:linear-gradient(160deg,#f4f5e8,#b4c15a)"></div><h4>Lorem Ipsum</h4><p>$ 150.00</p></div>
<div class="abs dots"><i class="on"></i><i></i><i></i><i></i><i></i></div>

<div class="abs ship-photo" role="img" aria-label="Scoop of formula powder over an open tin"></div>
<div class="abs ship-panel"></div>
<h2 class="abs ship-title">Free Shipping For<br>Orders Over $50</h2>
<p class="abs ship-text">Nemo enim ipsam voluptatem quia voluptas sit aspernatur aut odit aut fugit, sed quia consequuntur magni dolores eos qui ratione voluptatem sequi nesciunt.</p>
<a class="abs btn-white ship-btn">Shop Now</a>

<h2 class="abs section-title" style="top:2956px">What Clients Say</h2>
<p class="abs clients-sub">Risus commodo viverra maecenas accumsan lacus<br>accumsan vel facilisis.</p>
<span class="abs arrow" style="left:84px;top:3234px">‹</span>
<span class="abs arrow" style="left:1100px;top:3234px">›</span>
<div class="abs review" style="left:112px">
  <div class="meta">Lorem Ipsum : <span>02/07/2024</span></div><div class="stars">★★★★★</div>
  <p>Lorem ipsum dolor sit amet, consectetur adipiscing elit, sed do eiusmod tempor incididunt ut labore dolore magna aliqua. Quis ipsum suspendisse ultrices gravida.</p>
  <div class="who"><span class="avatar" role="img" aria-label="Client portrait" style="background:linear-gradient(135deg,#c77a3b,#5a2c14)"></span>Lorem Ipsum</div>
</div>
<div class="abs review" style="left:443px">
  <div class="meta">Lorem Ipsum : <span>02/07/2024</span></div><div class="stars">★★★★★</div>
  <p>Lorem ipsum dolor sit amet, consectetur adipiscing elit, sed do ut labore dolore magna aliqua.</p>
  <div class="who"><span class="avatar" role="img" aria-label="Client portrait" style="background:linear-gradient(135deg,#7a8a5c,#3b3528)"></span>Lorem Ipsum</div>
</div>
<div class="abs review" style="left:773px">
  <div class="meta">Lorem Ipsum : <span>02/07/2024</span></div><div class="stars">★★★★★</div>
  <p>Lorem ipsum dolor sit amet, consectetur adipiscing elit, sed do eiusmod tempor incididunt ut labore dolore magna aliqua. Quis ipsum suspendisse ultrices gravida.</p>
  <div class="who"><span class="avatar" role="img" aria-label="Client portrait" style="background:linear-gradient(135deg,#e9dcd2,#9b7a62)"></span>Lorem Ipsum</div>
</div>

<h2 class="abs news-title">Our Latest News</h2>
<span class="abs arrow" style="left:84px;top:3677px">‹</span>
<span class="abs arrow" style="left:1100px;top:3677px">›</span>
<article class="abs news" style="left:112px">
  <div class="news-img" role="img" aria-label="Toddler drinking from a bottle" style="background:linear-gradient(135deg,#eae6e0,#d9b9a0 55%,#c9c3b8)"></div>
  <div class="date">July 02 2024</div><h4>Risus commodo viverra maecenas accumsan facilisis.</h4><div class="more">Read More →</div>
</article>
<article class="abs news" style="left:443px">
  <div class="news-img" role="img" aria-label="Parent feeding a baby in a kitchen" style="background:linear-gradient(135deg,#f2f1ee,#d8c7b4 55%,#c4b09a)"></div>
  <div class="date">July 02 2024</div><h4>Risus commodo viverra maecenas accumsan facilisis.</h4><div class="more">Read More →</div>
</article>
<article class="abs news" style="left:773px">
  <div class="news-img" role="img" aria-label="Father bottle feeding a newborn" style="background:linear-gradient(135deg,#6d6a66,#d9d5cf 55%,#a9a39a)"></div>
  <div class="date">July 02 2024</div><h4>Risus commodo viverra maecenas accumsan facilisis.</h4><div class="more">Read More →</div>
</article>

<div class="abs brand footer-brand"><span class="brand-dot"></span><span class="brand-name">MILAVO</span></div>
<p class="abs footer-about">Lorem ipsum dolor sit amet, consectetur adipiscing elit, sed do eiusmod tempor incididunt ut labore et dolore magna</p>
<div class="abs footer-col" style="left:458px"><h5>Quick Links</h5><ul><li>Home</li><li>About Us</li><li>Shop</li><li>Products</li><li>Blog</li><li>Contact Us</li></ul></div>
<div class="abs footer-col" style="left:655px"><h5>Other Links</h5><ul><li>Support</li><li>Help</li><li>Faq</li><li>Terms and Conditions</li><li>Privacy Policy</li><li>Cookies Policy</li></ul></div>
<div class="abs footer-col" style="left:882px;width:215px"><h5>Contact Us</h5><ul><li style="line-height:22px">45 Meadow Lane, Springfield Baby Nutrition Co 10001.</li><li style="margin-top:8px">+1 555 010 0199</li><li style="margin-top:4px">hello@milavo.com</li></ul></div>
<a class="abs to-top">⌃</a>
<div class="abs copyright">© 2024, MILAVO</div>
<div class="abs socials"><i></i><i></i><i></i><i></i></div>

</body>
</html>
```